"Thornbury Accupuncture" needs a Promotional Card - A6 size

Requirements
Must have
• Bright colours, pictures of happy people, acupuncture-related pictures.

```html
<!DOCTYPE html>
<html lang="en">
<head>
<meta charset="utf-8">
<title>Thornbury Accupuncture – Promotional Card A6</title>
<link href="https://fonts.googleapis.com/css2?family=Arimo:wght@400;700&display=swap" rel="stylesheet">
<style>
  :root {
    --sky: #6ecbf0;
    --sky-deep: #3fb8ea;
    --orange: #f58a1f;
    --brand-red: #d8322a;
    --white: #ffffff;
    --ink-grey: #6f7378;
    --slate: rgba(58, 78, 102, 0.72);
    --slate-light: rgba(90, 112, 138, 0.55);
    --page: #ebe8e3;
  }
  * { box-sizing: border-box; margin: 0; padding: 0; }
  html, body { width: 1200px; height: 1000px; overflow: hidden; }
  body {
    background: var(--page);
    font-family: "Arimo", Arial, sans-serif;
    position: relative;
  }
  .card {
    position: absolute;
    overflow: hidden;
    box-shadow: 0 6px 18px rgba(0,0,0,0.18);
  }
  .photo { position: absolute; inset: 0; }

  /* Front card */
  .card-front { left: 40px; top: 20px; width: 800px; height: 540px; background: var(--white); }
  .card-front .photo {
    background: radial-gradient(ellipse at 40% 60%, #eccfb8 0%, #e8cdb9 28%, #f3efe9 55%, #f7f5f1 100%);
  }
  .headline-band {
    position: absolute; left: 0; right: 0; top: 40px; height: 135px;
    background: var(--sky);
  }
  .quote {
    position: absolute; display: flex; align-items: flex-start; gap: 10px;
    color: var(--white); font-weight: 700; line-height: 1.12;
  }
  .quote .mark {
    color: var(--orange); font-size: 78px; line-height: 0.8; font-weight: 700;
    font-family: Georgia, "Times New Roman", serif;
  }
  .quote .mark-close { align-self: flex-end; margin-bottom: -26px; }
  .card-front .quote { font-size: 27px; }
  .quote-wellbeing { left: 36px; top: 100px; }
  .quote-balance { left: 360px; top: 50px; }

  .call-line { position: absolute; left: 62px; top: 190px; display: flex; align-items: center; gap: 14px; }
  .call-label { color: var(--orange); font-size: 11px; line-height: 1.1; text-transform: uppercase; }
  .phone { color: var(--orange); font-size: 56px; font-weight: 400; letter-spacing: -1px; }

  .side-panel { position: absolute; left: 600px; top: 228px; width: 170px; height: 312px; }
  .relief-box { background: var(--sky-deep); height: 165px; padding: 30px 22px; }
  .relief-title { color: var(--orange); font-weight: 700; font-size: 17px; margin-bottom: 4px; }
  .relief-item { color: rgba(255,255,255,0.85); font-size: 17px; line-height: 1.4; }
  .brand-box { background: var(--white); height: 147px; padding: 24px 12px 0; text-align: center; }
  .brand-dot { display: block; width: 26px; height: 26px; border-radius: 50%; background: var(--orange); margin: 0 auto 8px; }
  .brand-name { color: var(--brand-red); font-weight: 700; font-size: 18px; line-height: 1; }
  .address { color: var(--ink-grey); font-size: 15px; margin-top: 8px; }

  /* Back card */
  .card-back { left: 500px; top: 575px; width: 660px; height: 410px; }
  .card-back .photo {
    background: linear-gradient(100deg, #a7c0d8 0%, #92aecb 40%, #c98a6c 62%, #d9a88c 78%, #8fa7c2 100%);
  }
  .overlay { position: absolute; }
  .back-brand {
    right: 20px; top: 16px; width: 200px; height: 112px;
    background: rgba(255,255,255,0.45); text-align: center; padding-top: 14px;
  }
  .back-brand .brand-dot { width: 22px; height: 22px; margin-bottom: 6px; }
  .back-brand .brand-name { font-size: 17px; }
  .back-brand .address { font-size: 13px; margin-top: 4px; }

  .card-back .quote { font-size: 20px; }
  .back-quote-top { left: 0; top: 92px; padding: 14px 20px 14px 28px; background: var(--slate); }
  .back-quote-top .mark, .back-quote-bottom .mark { font-size: 56px; }
  .back-quote-top .mark-close, .back-quote-bottom .mark-close { margin-bottom: -18px; }

  .back-relief {
    left: 0; top: 200px; width: 300px; height: 90px;
    background: var(--slate-light); padding: 12px 0 0 55px;
  }
  .back-relief .relief-title { color: var(--white); font-size: 13px; margin-bottom: 2px; }
  .back-relief .relief-item { font-size: 15px; line-height: 1.3; }
  .back-relief-more { left: 180px; top: 200px; padding: 12px 0 0 0; }
  .back-relief-more .relief-item { color: rgba(255,255,255,0.85); font-size: 15px; line-height: 1.3; }

  .doctor { left: 70px; top: 300px; width: 70px; text-align: left; }
  .doctor-photo {
    width: 68px; height: 78px; border: 3px solid var(--white);
    background: linear-gradient(180deg, #e9e3dc 0%, #b78b72 55%, #7b4a5e 100%);
  }
  .doctor-name { color: #3b4a5c; font-size: 10px; font-weight: 700; margin-top: 3px; white-space: nowrap; }
  .doctor-role { color: #3b4a5c; font-size: 9px; }

  .back-quote-bottom {
    left: 200px; top: 318px; padding: 12px 24px 14px 16px; background: var(--slate);
  }
</style>
</head>
<body>

  <section class="card card-front" aria-label="Promotional card front">
    <div class="photo" role="img" aria-label="Photo of a relaxed hand resting on a white towel with a fine acupuncture needle in the wrist"></div>
    <div class="headline-band"></div>

    <div class="quote quote-wellbeing">
      <span class="mark">“</span><span>Improve your<br>well-being</span><span class="mark mark-close">”</span>
    </div>
    <div class="quote quote-balance">
      <span class="mark">“</span><span>Improve your physical<br>&amp; emotional balance.</span><span class="mark mark-close">”</span>
    </div>

    <div class="call-line">
      <span class="call-label">Call us<br>today</span>
      <span class="phone">123-456-7890</span>
    </div>

    <aside class="side-panel">
      <div class="relief-box">
        <p class="relief-title">Relief For</p>
        <p class="relief-item">Back Pain</p>
        <p class="relief-item">Headaches</p>
        <p class="relief-item">Weight Loss</p>
        <p class="relief-item">Insomnia</p>
      </div>
      <div class="brand-box">
        <span class="brand-dot"></span>
        <p class="brand-name">Thornbury<br>Accupuncture</p>
        <p class="address">123 Street Name</p>
      </div>
    </aside>
  </section>

  <section class="card card-back" aria-label="Promotional card back">
    <div class="photo" role="img" aria-label="Photo of a smiling red-haired senior woman against a soft blue background"></div>

    <div class="overlay back-brand">
      <span class="brand-dot"></span>
      <p class="brand-name">Thornbury<br>Accupuncture</p>
      <p class="address">123 Street Name</p>
    </div>

    <div class="overlay quote back-quote-top">
      <span class="mark">“</span><span>Improve your<br>well-being</span><span class="mark mark-close">”</span>
    </div>

    <div class="overlay back-relief">
      <p class="relief-title">Relief For</p>
      <p class="relief-item">Back Pain</p>
      <p class="relief-item">Headaches</p>
    </div>
    <div class="overlay back-relief-more">
      <p class="relief-item">Weight Loss</p>
      <p class="relief-item">Insomnia</p>
    </div>

    <div class="overlay doctor">
      <div class="doctor-photo" role="img" aria-label="Portrait photo of the specialist"></div>
      <p class="doctor-name">Dr Name here</p>
      <p class="doctor-role">Specialist</p>
    </div>

    <div class="overlay quote back-quote-bottom">
      <span class="mark">“</span><span>Improve your physical<br>&amp; emotional balance.</span><span class="mark mark-close">”</span>
    </div>
  </section>

</body>
</html>
```